Provide bookkeeping and accounting services to small and growing businesses

We need website and logo design using the name Dornaby as the logo.
The target audience are small companies and startups who need:
1) Simple bookkeeping services
2) Accounting advice that only someone with many years of senior financial experience as a CPA can provide.

The services are provided by two individuals. each of whom specialize in one of the areas.

We want the website to be clean without a lot of visual distraction but don't know how to make a boring subject interesting. We believe our potential clients, small business owners, need to find what they want quickly and easily without a lot of verbiage or distractions.

We've attached a draft of the homepage and have completed the text on most of the other pages.

Target Market(s)

small and early stage growth companies in San Diego North County

Industry/Entity Type

Accounting

Number of Pages Required

1 page

Font styles to use
Sans Serif

Colors
86cfc6
33b8a4
85cae6

Requirements
Must have
• We need a design for the website homepage that includes the name Dornaby as the logo. Must include a design for the name.
• Must have color in teal or greenish blue.
Nice to have
• White background, clean, clear, uncluttered.
• We would like to use the design in a Theme on a WordPress website. Themes Paper Lantern and Quiet Harbour are appealing to us.
Should not have
• Moving pictures

```html
<!DOCTYPE html>
<html lang="en">
<head>
<meta charset="utf-8">
<title>Dornaby Accounting and Bookkeeping</title>
<link rel="stylesheet" href="https://fonts.googleapis.com/css2?family=Ubuntu:wght@300;400;500&family=Lato:wght@400;700&display=swap">
<style>
:root{
  --teal:#33b8a4;
  --teal-soft:#86cfc6;
  --teal-active:#6fc3b7;
  --sky:#85cae6;
  --ink:#222;
  --body:#333;
  --muted:#999;
  --footer:#1d1d1d;
  --footer-line:#3a3a3a;
  --white:#fff;
}
*{box-sizing:border-box;margin:0;padding:0}
html,body{width:1200px;height:2344px;overflow:hidden;background:var(--white)}
body{position:relative;font-family:"Lato",sans-serif;color:var(--body)}
.abs{position:absolute}
.heading{font-family:"Ubuntu",sans-serif;font-weight:400}

/* header */
.brand-name{left:102px;top:6px;font-family:"Ubuntu",sans-serif;font-size:48px;color:var(--teal);line-height:1.1}
.brand-tag{left:101px;top:62px;font-size:17px;color:#333}
.contact-chip{top:26px;display:flex;gap:12px;font-size:15px;color:#222;line-height:20px}
.contact-chip svg{width:38px;height:42px}

/* nav */
.main-nav{left:0;top:103px;width:1200px;height:42px;background:var(--teal-soft)}
.nav-item{top:0;height:42px;line-height:42px;text-align:center;color:var(--white);font-size:17px;border-right:1px solid rgba(255,255,255,.35)}
.nav-item.active{background:var(--teal-active)}

/* hero */
.hero{left:0;top:145px;width:1200px;height:539px;background:linear-gradient(100deg,#4d4a3a 0%,#8a8173 30%,#b7b6b0 50%,#7c6652 75%,#4b3a2e 100%)}
.hero-title{left:100px;top:330px;width:1000px;text-align:center;color:var(--white);font-family:"Ubuntu",sans-serif;font-size:39px;line-height:50px;text-shadow:0 2px 4px rgba(0,0,0,.6)}
.slider-dots{left:572px;top:652px;display:flex;gap:8px}
.slider-dots span{width:10px;height:10px;border-radius:50%;background:rgba(255,255,255,.6)}
.slider-dots span.on{background:var(--white)}

/* section titles */
.section-title{width:1200px;left:0;text-align:center;font-size:33px;color:var(--ink)}
.section-title em{font-style:normal;color:var(--teal)}
.title-rule{left:380px;width:440px;height:10px}

.welcome-copy{left:102px;top:803px;width:994px;text-align:center;font-size:13.5px;line-height:25px;color:#333}
.btn{display:flex;align-items:center;justify-content:center;gap:8px;color:var(--white);font-size:13px;font-weight:700;border-radius:2px}
.btn .arrow{width:18px;height:18px;border-radius:50%;background:var(--white);display:flex;align-items:center;justify-content:center}
.btn-sky{background:var(--sky)}

/* services */
.services-band{left:0;top:1008px;width:1200px;height:406px;background:var(--teal)}
.services-title{left:102px;top:1038px;font-size:34px;color:var(--white)}
.service-icon{width:126px;height:126px;border-radius:50%;background:rgba(255,255,255,.35);display:flex;align-items:center;justify-content:center}
.service-name{font-size:19px;font-weight:700;color:var(--white)}
.service-text{font-size:14px;line-height:20px;color:var(--white);width:290px}
.btn-ghost{width:94px;height:34px;border:1px solid rgba(255,255,255,.7);background:rgba(255,255,255,.2);color:var(--white);font-size:14px;display:flex;align-items:center;justify-content:center}

/* inquiry */
.inquiry-card{left:795px;top:1047px;width:305px;height:331px;background:var(--white);box-shadow:0 4px 10px rgba(0,0,0,.2)}
.inquiry-tab{left:809px;top:1039px;width:277px;height:41px;background:var(--sky);color:var(--white);font-family:"Ubuntu",sans-serif;font-size:23px;text-align:center;line-height:41px}
.field{left:819px;width:264px;border:1px solid #e3e3e3;background:linear-gradient(#fff,#f5f5f5);font-size:14px;color:#444;display:flex}
.field .ico{width:36px;border-right:1px solid #e3e3e3;display:flex;justify-content:center;padding-top:10px}
.field .lbl{padding:9px 0 0 10px}

/* reviews */
.review-avatar{width:84px;height:84px;border-radius:50%;border:3px solid #ddd;background:linear-gradient(#d9c7b5,#a88e78)}
.review-quote{width:360px;font-size:15.5px;line-height:23px;color:#222}
.review-quote .qm{font-family:"Ubuntu",sans-serif;font-size:40px;color:#ccc;line-height:0;vertical-align:-14px}
.review-author{font-size:16px;font-weight:700;color:var(--teal)}
.review-split{left:600px;top:1555px;width:1px;height:130px;background:#e6e6e6}

/* cta */
.cta-band{left:0;top:1767px;width:1200px;height:281px;background:linear-gradient(90deg,#86c6e2,#9ccfe6 45%,#7fbfdc)}
.cta-text{left:100px;top:1803px;width:1000px;text-align:center;color:var(--white);font-family:"Ubuntu",sans-serif;font-size:31px;line-height:45px;font-weight:300}
.btn-teal{background:var(--teal);font-size:16px;font-weight:700}

/* footer */
.site-footer{left:0;top:2048px;width:1200px;height:252px;background:var(--footer)}
.foot-title{font-family:"Ubuntu",sans-serif;font-size:17px;color:#eee}
.foot-rule{height:1px;background:var(--footer-line);top:2106px}
.foot-sep{top:2080px;width:1px;height:190px;background:#2c2c2c}
.foot-links{left:102px;top:2116px;list-style:none;font-size:12.5px;color:#ddd;line-height:23.7px}
.foot-links li::before{content:"›";margin-right:10px;color:#aaa}
.foot-contact{font-size:12.5px;color:#eee;line-height:18px}
.map-area{left:583px;top:2122px;width:255px;height:136px;background:linear-gradient(135deg,#e9e6dc,#d9dfd3 60%,#c9d9e3);border:2px solid #ccc}
.foot-brand{left:900px;top:2138px;width:216px;text-align:center;font-family:"Ubuntu",sans-serif;font-size:37px;color:#bbb}
.foot-brand-tag{left:900px;top:2186px;width:216px;text-align:center;font-size:13px;color:#bbb}
.social-dot{top:2218px;width:25px;height:25px;border-radius:50%}
.copyright{left:0;top:2300px;width:1200px;height:44px;background:var(--teal);color:var(--white);font-size:13px;text-align:center;line-height:44px}
</style>
</head>
<body>

<header>
  <div class="abs brand-name">Dornaby</div>
  <div class="abs brand-tag">Accounting and Bookkeeping</div>
  <div class="abs contact-chip" style="left:752px">
    <svg viewBox="0 0 38 42" fill="none" stroke="#33b8a4" stroke-width="2.4"><circle cx="19" cy="22" r="17"/><path d="M12 13c-3 4 0 12 6 17 4 3 8 3 9 1l-4-4-3 2c-3-2-5-5-6-8l2-3-4-5z" fill="#33b8a4" stroke="none"/></svg>
    <div>Call Us:<br>(012) 555 0142</div>
  </div>
  <div class="abs contact-chip" style="left:912px">
    <svg viewBox="0 0 38 42" fill="none" stroke="#33b8a4" stroke-width="2.4"><path d="M3 16l20-12 12 10v20l-32 4z"/><path d="M3 16l17 12 15-14"/></svg>
    <div>Mail Us:<br>info@dornaby.com</div>
  </div>
</header>

<nav class="abs main-nav">
  <div class="abs nav-item active" style="left:98px;width:150px">Home</div>
  <div class="abs nav-item" style="left:248px;width:174px">About Us</div>
  <div class="abs nav-item" style="left:422px;width:169px">Services</div>
  <div class="abs nav-item" style="left:591px;width:143px">Experience</div>
  <div class="abs nav-item" style="left:734px;width:175px">Resources</div>
  <div class="abs nav-item" style="left:909px;width:188px">Contact Us</div>
</nav>

<section>
  <div class="abs hero" role="img" aria-label="Photo of hands working a calculator beside a laptop on a wooden desk"></div>
  <h1 class="abs hero-title" style="font-weight:400">Providing a full range of accounting, tax, bookkeeping and business consulting services</h1>
  <div class="abs slider-dots"><span class="on"></span><span></span></div>
</section>

<section>
  <h2 class="abs section-title heading" style="top:726px">Welcome To <em>Dornaby</em> Accounting and Bookkeeping</h2>
  <svg class="abs title-rule" style="top:775px" viewBox="0 0 440 10"><line x1="0" y1="5" x2="210" y2="5" stroke="#ccc"/><line x1="230" y1="5" x2="440" y2="5" stroke="#ccc"/><circle cx="220" cy="5" r="4" fill="#bbb"/></svg>
  <p class="abs welcome-copy">Lorem ipsum dolouar sit amet consec tetuer adipiscing elnit. Praebulum molesbeutie lacus. Aenea nonuendrerit maurihasellu porta. Fusce suscpvarius mi. Cum sociis natoque penatibus et magnis dis parturientontes nascetur ridiculus mus. Nulla dui. Fusce feugiat mal esuada odio. Morbi nunc odio gravida atcursus necuctus a lorem. Maecenas tristique orci ac sem uis ultricies pharetra magna. Donec accumsan malesuada orci.onec sit amet eros. Lorem ipsu m dolor sit amet consectetuer adipiscing elit. Mauris fermentum dictum reet aliquam leo tellus dolor dapibus eget elementum vel cursus eleifend elit.</p>
  <div class="abs btn btn-sky" style="left:539px;top:923px;width:119px;height:35px">READ MORE <span class="arrow"><svg width="8" height="10" viewBox="0 0 8 10"><path d="M2 1l4 4-4 4" stroke="#85cae6" stroke-width="2" fill="none"/></svg></span></div>
</section>

<section>
  <div class="abs services-band"></div>
  <h2 class="abs services-title heading">Our Services</h2>
  <div class="abs" style="left:312px;top:1065px;width:422px;height:1px;background:rgba(255,255,255,.6)"></div>
  <svg class="abs" style="left:290px;top:1105px" width="160" height="120" viewBox="0 0 160 120" stroke="#fff" stroke-width="1.5" fill="#fff"><line x1="83" y1="4" x2="83" y2="68" fill="none"/><line x1="10" y1="111" x2="150" y2="111" fill="none"/><path d="M4 111l10-6v12z" stroke="none"/><path d="M156 111l-10-6v12z" stroke="none"/></svg>

  <div class="abs service-icon" style="left:115px;top:1114px">
    <svg width="70" height="76" viewBox="0 0 70 76" fill="none" stroke="#fff" stroke-width="3"><rect x="22" y="18" width="40" height="54" rx="4"/><rect x="29" y="25" width="26" height="10"/><g fill="#fff" stroke="none"><rect x="29" y="42" width="6" height="6"/><rect x="39" y="42" width="6" height="6"/><rect x="49" y="42" width="6" height="6"/><rect x="29" y="52" width="6" height="6"/><rect x="39" y="52" width="6" height="6"/><rect x="49" y="52" width="6" height="6"/><rect x="29" y="62" width="6" height="6"/><rect x="39" y="62" width="6" height="6"/><rect x="49" y="62" width="6" height="6"/></g><path d="M18 10c-6-3-12 0-11 5s11 4 11 10-8 7-12 4M12 4v34"/></svg>
  </div>
  <div class="abs service-name" style="left:98px;top:1254px">Simple bookkeeping</div>
  <p class="abs service-text" style="left:98px;top:1287px">Lorem ipsum dolouar sit amet consec tetuerrt scing elnit. Praebulum molesbeutie lacus.</p>
  <div class="abs btn-ghost" style="left:98px;top:1341px">Read More</div>

  <div class="abs service-icon" style="left:481px;top:1114px">
    <svg width="64" height="76" viewBox="0 0 64 76" fill="none" stroke="#fff" stroke-width="3"><path d="M18 4h30l12 12v56H18z"/><path d="M10 12v60h40" /><path d="M48 4v12h12"/><line x1="38" y1="32" x2="52" y2="32"/><line x1="38" y1="42" x2="52" y2="42"/><line x1="26" y1="54" x2="52" y2="54"/><line x1="26" y1="62" x2="52" y2="62"/><path d="M34 30c-3-2-8-1-8 2s8 3 8 6-5 4-8 2M30 26v18"/></svg>
  </div>
  <div class="abs service-name" style="left:472px;top:1254px">Accounting advice</div>
  <p class="abs service-text" style="left:472px;top:1287px">Lorem ipsum dolouar sit amet consec tetuerrt scing elnit. Praebulum molesbeutie lacus.</p>
  <div class="abs btn-ghost" style="left:472px;top:1341px">Read More</div>

  <form>
    <div class="abs inquiry-card"></div>
    <div class="abs inquiry-tab">Quick Inquiry</div>
    <div class="abs field" style="top:1094px;height:34px"><span class="ico"><svg width="12" height="12" viewBox="0 0 12 12" fill="#999"><circle cx="6" cy="3.5" r="3"/><path d="M0 12c0-4 3-5 6-5s6 1 6 5z"/></svg></span><span class="lbl">Name</span></div>
    <div class="abs field" style="top:1138px;height:34px"><span class="ico"><svg width="12" height="12" viewBox="0 0 12 12" fill="#999"><path d="M2 0l3 3-1.5 2c1 2 2 3 4 4L9.5 7.5l2.5 3-2 1.5C5 12 0 7 0 2z"/></svg></span><span class="lbl">Phone</span></div>
    <div class="abs field" style="top:1180px;height:34px"><span class="ico"><svg width="13" height="10" viewBox="0 0 13 10" fill="none" stroke="#999" stroke-width="1.5"><rect x="1" y="1" width="11" height="8"/><path d="M1 1l5.5 4 5.5-4"/></svg></span><span class="lbl">Email</span></div>
    <div class="abs field" style="top:1225px;height:84px"><span class="ico"><svg width="12" height="12" viewBox="0 0 12 12" fill="none" stroke="#999" stroke-width="1.4"><path d="M1 3v8h8V7M5 8l1-3 5-5 1 1-5 5z"/></svg></span><span class="lbl">Message</span></div>
    <div class="abs btn btn-sky" style="left:819px;top:1327px;width:119px;height:34px">READ MORE <span class="arrow"><svg width="8" height="10" viewBox="0 0 8 10"><path d="M2 1l4 4-4 4" stroke="#85cae6" stroke-width="2" fill="none"/></svg></span></div>
  </form>
</section>

<section>
  <h2 class="abs section-title heading" style="top:1455px">Customer <em>Reviews</em></h2>
  <svg class="abs title-rule" style="top:1506px" viewBox="0 0 440 10"><line x1="0" y1="5" x2="210" y2="5" stroke="#ccc"/><line x1="230" y1="5" x2="440" y2="5" stroke="#ccc"/><circle cx="220" cy="5" r="4" fill="#bbb"/></svg>

  <svg class="abs" style="left:54px;top:1591px" width="18" height="38" viewBox="0 0 18 38"><path d="M16 2L2 19l14 17" stroke="#aaa" stroke-width="2" fill="none"/></svg>
  <svg class="abs" style="left:1126px;top:1591px" width="18" height="38" viewBox="0 0 18 38"><path d="M2 2l14 17-14 17" stroke="#aaa" stroke-width="2" fill="none"/></svg>

  <div class="abs review-avatar" style="left:100px;top:1570px" role="img" aria-label="Portrait of client Maren"></div>
  <p class="abs review-quote" style="left:203px;top:1550px"><span class="qm">“</span>&nbsp; Lorem ipsum dolor sit amet, onsectietuer icingr eliterei sed diam nonummy nibh euismod tincideuntr ut laoreet dolore gna roerererweire aliquam eraterer lutpatei. Uti wisi enim ad miwinim veniam, quiserere istrud wer rreri tation. <span class="qm">”</span></p>
  <div class="abs review-author" style="left:203px;top:1679px">- Maren</div>

  <div class="abs review-split"></div>

  <div class="abs review-avatar" style="left:630px;top:1570px" role="img" aria-label="Portrait of client Tobias"></div>
  <p class="abs review-quote" style="left:733px;top:1550px"><span class="qm">“</span>&nbsp; Lorem ipsum dolor sit amet, onsectietuer icingr eliterei sed diam nonummy nibh euismod tincideuntr ut laoreet dolore gna roerererweire aliquam eraterer lutpatei. Uti wisi enim ad miwinim veniam, quiserere istrud wer rreri tation. <span class="qm">”</span></p>
  <div class="abs review-author" style="left:733px;top:1679px">- Tobias</div>
</section>

<section>
  <div class="abs cta-band" role="img" aria-label="Soft blue backdrop of a business person overlooking hills"></div>
  <p class="abs cta-text">Dornaby offers a flexible range of accounting and bookkeeping services and support&nbsp; for small and growing organizations in San Diego North County.</p>
  <div class="abs btn btn-teal" style="left:530px;top:1966px;width:139px;height:37px">Call Us Today <span class="arrow"><svg width="8" height="10" viewBox="0 0 8 10"><path d="M2 1l4 4-4 4" stroke="#33b8a4" stroke-width="2" fill="none"/></svg></span></div>
</section>

<footer>
  <div class="abs site-footer"></div>
  <div class="abs foot-sep" style="left:265px"></div>
  <div class="abs foot-sep" style="left:538px"></div>
  <div class="abs foot-sep" style="left:876px"></div>

  <div class="abs foot-title" style="left:102px;top:2076px">Quick Links</div>
  <div class="abs foot-rule" style="left:102px;width:152px"></div>
  <ul class="abs foot-links">
    <li>Home</li><li>About Us</li><li>Services</li><li>Experience</li><li>Resources</li><li>Contact Us</li>
  </ul>

  <div class="abs foot-title" style="left:294px;top:2076px">Contact Information</div>
  <div class="abs foot-rule" style="left:294px;width:206px"></div>
  <svg class="abs" style="left:292px;top:2124px" width="12" height="16" viewBox="0 0 12 16"><path d="M6 0a6 6 0 0 0-6 6c0 4 6 10 6 10s6-6 6-10a6 6 0 0 0-6-6z" fill="#33b8a4"/><circle cx="6" cy="6" r="2" fill="#1d1d1d"/></svg>
  <div class="abs foot-contact" style="left:318px;top:2122px;font-weight:700">DORNABY<br><span style="font-weight:700">123 euismod cidun ut laoreet<br>laoreet dol magna aliquam</span></div>
  <svg class="abs" style="left:292px;top:2198px" width="13" height="14" viewBox="0 0 12 12" fill="#33b8a4"><path d="M2 0l3 3-1.5 2c1 2 2 3 4 4L9.5 7.5l2.5 3-2 1.5C5 12 0 7 0 2z"/></svg>
  <div class="abs foot-contact" style="left:318px;top:2197px;font-size:14px">(012) 555 0142</div>
  <svg class="abs" style="left:292px;top:2239px" width="14" height="10" viewBox="0 0 13 10" fill="#33b8a4"><rect width="13" height="10"/><path d="M0 0l6.5 5L13 0" stroke="#1d1d1d" fill="none"/></svg>
  <div class="abs foot-contact" style="left:318px;top:2235px">info@dornaby.com</div>

  <div class="abs foot-title" style="left:580px;top:2076px">Location Map</div>
  <div class="abs foot-rule" style="left:580px;width:250px"></div>
  <div class="abs map-area" role="img" aria-label="Street map showing the office location"></div>

  <div class="abs foot-brand">Dornaby</div>
  <div class="abs foot-brand-tag">Accounting and Bookkeeping</div>
  <div class="abs social-dot" style="left:946px;background:#3b5a9a" aria-label="Social profile"></div>
  <div class="abs social-dot" style="left:979px;background:#1a7bb5" aria-label="Social profile"></div>
  <div class="abs social-dot" style="left:1011px;background:#2aa3e0" aria-label="Social profile"></div>
  <div class="abs social-dot" style="left:1045px;background:#d9432f" aria-label="Social profile"></div>

  <div class="abs copyright">Copyright © 2016 Dornaby Accounting and Bookkeeping.&nbsp; All Rights Reserved.</div>
</footer>

</body>
</html>
```